Marlowe Group needs a business card

I would like the card to be simple but modern and elegant.
I like black and white.
or black and gold.
we are a private finance lender and also are involved in property and property developments.

please look at the business card photos i provided i would like M.G only one one side and all the other details on the other side use fonts that tie in with my theme.

Industry/Entity Type

Finance

Contact Information for Business Card

Marlowe Group (M.G) Daniel Marlowe M: 0413586207 E: danmarl@inboxmail.test

Font styles to use
Other font styles liked:
• Use fonts that would reflect our business

Colors
000000
ffffff

Requirements
Must have
• one side of details
• other side has either M.G or Marlowe Group like in the photos provided

```html
<!DOCTYPE html>
<html lang="en">
<head>
<meta charset="utf-8">
<title>Marlowe Group – Business Card</title>
<link href="https://fonts.googleapis.com/css2?family=Open+Sans:wght@400;700;800&display=swap" rel="stylesheet">
<style>
  :root {
    --backdrop: #d8d3cb;
    --card-face: #eef0f1;
    --ink: #111111;
    --ink-soft: #2a2a2a;
    --arc-grey: #8a8a8a;
  }
  html, body {
    margin: 0;
    padding: 0;
    width: 1200px;
    height: 969px;
    overflow: hidden;
    background: var(--backdrop);
    font-family: "Open Sans", Arial, sans-serif;
  }
  .canvas {
    position: relative;
    width: 1200px;
    height: 969px;
  }
  .business-card {
    position: absolute;
    left: 100px;
    top: 200px;
    width: 1000px;
    height: 568px;
    border-radius: 36px;
    background: var(--card-face);
    overflow: hidden;
    box-shadow: 0 6px 24px rgba(0,0,0,0.12);
  }
  .corner-art {
    position: absolute;
    inset: 0;
    width: 100%;
    height: 100%;
  }
  .brand-name {
    position: absolute;
    left: 60px;
    top: 62px;
    color: var(--ink);
    font-weight: 800;
    line-height: 1;
    text-transform: uppercase;
  }
  .brand-name .brand-main {
    display: block;
    font-size: 72px;
    letter-spacing: 2px;
  }
  .brand-name .brand-sub {
    display: block;
    margin-top: 10px;
    font-size: 30px;
    letter-spacing: 10px;
    padding-left: 4px;
  }
  .contact-block {
    position: absolute;
    right: 52px;
    top: 362px;
    text-align: right;
    color: var(--ink-soft);
  }
  .contact-name {
    margin: 0 0 14px;
    font-size: 35px;
    font-weight: 700;
    color: var(--ink);
  }
  .contact-line {
    margin: 0;
    font-size: 25px;
    line-height: 38px;
  }
  .contact-label {
    font-weight: 700;
  }
</style>
</head>
<body>
<div class="canvas">
  <section class="business-card" aria-label="Marlowe Group business card">
    <svg class="corner-art" viewBox="0 0 582 330" preserveAspectRatio="none" aria-hidden="true">
      <path d="M455,0 H582 V125 C560,70 520,25 455,0 Z" fill="var(--ink)"/>
      <path d="M443,2 C518,30 566,80 579,138" fill="none" stroke="var(--arc-grey)" stroke-width="3"/>
      <path d="M0,200 C20,260 60,305 125,330 H0 Z" fill="var(--ink)"/>
      <path d="M3,193 C20,255 65,305 137,328" fill="none" stroke="var(--arc-grey)" stroke-width="3"/>
    </svg>

    <div class="brand-name">
      <span class="brand-main">Marlowe</span>
      <span class="brand-sub">Group</span>
    </div>

    <div class="contact-block">
      <p class="contact-name">Daniel Marlowe</p>
      <p class="contact-line"><span class="contact-label">Cell :</span> 0413586207</p>
      <p class="contact-line">danmarl@inboxmail.test</p>
      <p class="contact-line">www.marlowegroup.test</p>
    </div>
  </section>
</div>
</body>
</html>
```